Equipment Finance Specialist I work with companies who need the funds to buy their equipment

I would like a business card that stands out on the shelves. I want to be able to hand it to someone and say WOW. This card should have my logo.
You can put color into it I am very open on design and color

What my company does is we deal with dealerships that sell equipment such as Dump Trucks garbage trucks tractors trailers. Customers get referred to us and depending on their time in business we will ask for the following items

Companies that have been in business for more than two years we have a credit application program up to 250K . With this program we need the following items Credit application filled out(which is what I would like to be able for the customer to click on my website to get.) as well as three current month bank statements.

Deals over 250k we will need the following items

2 years business tax returns
2 years personal tax returns
Profit & Loss statement
Personal Financial Statement

what we do
100% FINANCING
SEASONAL PAYMENTS
LOAN BALLOON PAYMENTS
TRAC LEASING
LOW-INTEREST REFINANCING RATES
DEBT CONSOLIDATION

We specialize in creative financing solutions and offer a variety of reliable, flexible and expandable lending choices.

Target Market(s)

Trucking Companies

Industry/Entity Type

Trucking Company

Contact Information for Business Card

* $250,000 Application only Program
* Loans from $30,000 to 5,000,000
* Competitive Interest Rates

Font styles to use
Serif
Sans Serif

Colors

Designer to choose colors to be used in the design.

Requirements
Must have
• On the back of the card.
• * $250,000 Application only Program
• * Loans from $30,000 to 5,000,000
• My name, email, website. address
• * Competitive Interest Rates
• * 100% Financing
Nice to have
• I want my logo to pop on the card
• My logo is the great one I would like to use
Should not have
• I am up for your creativity as well

```html
<!DOCTYPE html>
<html lang="en">
<head>
<meta charset="utf-8">
<title>Summit Lending – Business Card</title>
<link rel="stylesheet" href="https://fonts.googleapis.com/css2?family=Saira:wght@500;600;700&family=Open+Sans:wght@400&display=swap">
<style>
  :root {
    --page-bg: #e9e9e9;
    --navy: #0d2a6b;
    --red: #c8102e;
    --text-gray: #5a5a5a;
    --card-white: #ffffff;
    --card-black: #1b1c1e;
    --faint-blue: #e6ebf3;
    --silver: #d9dbde;
    --silver-dark: #9a9ea3;
  }
  * { box-sizing: border-box; margin: 0; padding: 0; }
  html, body { width: 1125px; height: 1200px; overflow: hidden; background: var(--page-bg); }
  .canvas { position: relative; width: 1125px; height: 1200px; }

  .card { position: absolute; left: 150px; width: 826px; height: 471px; overflow: hidden; }
  .card-front { top: 98px; background: var(--card-white); }
  .card-back { top: 631px; background: var(--card-black); }

  /* front */
  .brand-mark {
    position: absolute; left: 58px; top: 52px; width: 118px; height: 118px;
    border-radius: 50%; background: var(--navy);
  }
  .brand-name {
    position: absolute; left: 196px; top: 62px;
    font-family: "Saira", sans-serif; font-weight: 700; font-size: 44px; line-height: 46px;
    color: var(--navy); letter-spacing: 1px;
  }
  .side-band {
    position: absolute; left: 56px; top: 170px; width: 127px; height: 301px;
    background: var(--navy);
    clip-path: polygon(0 0, 100% 0, 99% 100%, 0 100%);
  }
  .band-icon { position: absolute; left: 52px; width: 24px; height: 24px; fill: #fff; }
  .faint-decoration {
    position: absolute; left: 450px; top: 40px; width: 500px; height: 500px;
    border-radius: 50%; background: radial-gradient(circle at 45% 45%, var(--faint-blue), #f3f5f9 70%);
  }
  .contact { position: absolute; left: 210px; font-family: "Saira", sans-serif; }
  .contact-name { top: 205px; font-size: 29px; font-weight: 700; color: var(--navy); letter-spacing: .3px; }
  .contact-title { top: 240px; font-size: 21px; font-weight: 600; color: var(--red); letter-spacing: .5px; }
  .contact-address { top: 282px; font-size: 20px; font-weight: 500; color: var(--text-gray); line-height: 26px; }
  .contact-phone { top: 346px; left: 212px; font-size: 21px; font-weight: 600; color: var(--text-gray); letter-spacing: .6px; }
  .contact-web { top: 378px; left: 212px; font-size: 19px; font-weight: 500; color: var(--text-gray); line-height: 27px; }

  /* back */
  .back-mark {
    position: absolute; left: 268px; top: 115px; width: 90px; height: 90px; border-radius: 50%;
    background: linear-gradient(135deg, var(--silver), var(--silver-dark));
  }
  .back-brand {
    position: absolute; left: 375px; top: 118px;
    font-family: "Saira", sans-serif; font-weight: 700; font-size: 40px; line-height: 42px;
    color: var(--silver); letter-spacing: 1px;
  }
  .offer-list {
    position: absolute; left: 0; right: 0; top: 394px; text-align: center;
    font-family: "Open Sans", sans-serif; font-size: 20px; line-height: 26px; color: #f2f2f2;
  }
  .offer-list .dot { font-size: 14px; vertical-align: 2px; }
</style>
</head>
<body>
<div class="canvas">

  <section class="card card-front" aria-label="Business card front">
    <div class="faint-decoration" role="img" aria-label="Faint background area for the company emblem"></div>
    <div class="brand-mark" aria-hidden="true"></div>
    <div class="brand-name">SUMMIT<br>LENDING</div>

    <div class="side-band">
      <svg class="band-icon" style="top:68px" viewBox="0 0 24 24" aria-hidden="true"><circle cx="12" cy="7" r="5"/><path d="M2 23c0-6 4-9 10-9s10 3 10 9z"/></svg>
      <svg class="band-icon" style="top:138px" viewBox="0 0 24 24" aria-hidden="true"><path d="M12 1a8 8 0 0 0-8 8c0 6 8 14 8 14s8-8 8-14a8 8 0 0 0-8-8zm0 11a3 3 0 1 1 0-6 3 3 0 0 1 0 6z"/></svg>
      <svg class="band-icon" style="top:197px" viewBox="0 0 24 24" aria-hidden="true"><path d="M2 8c0-3 4-4 10-4s10 1 10 4v2h-5V8H7v2H2z"/><path d="M6 11h12l2 10H4z"/><circle cx="12" cy="16" r="3" fill="#0d2a6b"/></svg>
      <svg class="band-icon" style="top:226px" viewBox="0 0 24 24" aria-hidden="true"><path d="M2 6h20v12H2z"/><path d="M2 6l10 7 10-7" fill="none" stroke="#0d2a6b" stroke-width="2"/></svg>
      <svg class="band-icon" style="top:254px" viewBox="0 0 24 24" aria-hidden="true"><circle cx="12" cy="12" r="10"/><path d="M7 6c2 2 0 4 3 5s1 4 3 5M15 4c0 3 3 3 4 6" fill="none" stroke="#0d2a6b" stroke-width="2"/></svg>
    </div>

    <div class="contact contact-name">MARK ELLISON</div>
    <div class="contact contact-title">PRESIDENT</div>
    <div class="contact contact-address">4127 Harbor View Lane<br>Cedar Grove, NJ 07009</div>
    <div class="contact contact-phone">555 014 3386</div>
    <div class="contact contact-web">mark@summitlending.com<br>www.summitlending.com</div>
  </section>

  <section class="card card-back" aria-label="Business card back">
    <div class="back-mark" aria-hidden="true"></div>
    <div class="back-brand">SUMMIT<br>LENDING</div>
    <p class="offer-list">
      $250,000 Application only Program<span class="dot">●</span> Loans from $30,000 to 5,000,000<br>
      Competitive Interest Rates <span class="dot">●</span>100% Financing
    </p>
  </section>

</div>
</body>
</html>
```